Electrictrian Contractor Website Design

We are working with an electrical contractor in California called Fennick Electric.

Some sites to use for content/competitors and inspiration:
https://corvanelectric.example
https://tralvenpage.example/web/contractor/ (lots of contractor website designs we've approved and continue to show clients)

Thank you for taking the time to consider designing a website for us. We are web developers based in Stockton, CA, USA. Most of our projects go through the same process. Understanding this process may help you win a project with us. We custom-code all of our websites in-house. We don’t have any requirements as to what tools you use for your design, but we prefer Figma files. For any design that we label as four-stars, we send it to the client for review. The client picks the final design they want us to use. Once we complete this process, we will continue to show additional clients all the four-star sites and purchase them later. Your designs will have multiple chances to sell. For better chances of success, we ask that you follow these guidelines.

IMAGES:
If you use any images or icons in the design, we ask that you have a link to the asset so we can purchase the image/icon. Most of the designs we submit do not have the customer’s images on them unless they have some great images. Be creative; show us the feeling you are trying to portray with your image choices. Use any royalty-free site you choose. We subscribe to Quorvane and mainly use their images, but we can purchase images outside of Quorvane.

PLEASE NOTE: we will not submit designs to clients with watermarks on the images.

FONTS:
We ask that you identify the fonts used in the design. This can be done in a message if you want. We typically use Pellmarsh Type and Quorvane Type.

CONTENT:
We're always open to different content and ideas. We often submit designs with stock images so the client can see our vision. We typically take pictures after the website launch to use their images with our vision. Lorem Ipsum is fine for paragraphs, but we ask that you write the headers in correct English. We want to be able to show the vision and identify the sections of the website.

INSPIRATION:
We typically add a couple of links in the brief of websites we like to help you get started in your design.

REVISIONS:
We do not often ask for revisions of the designs unless we see something in the design that may not appeal to the client. If there are slight changes that we want to make, we do that in the development process.

FEEDBACK:
We rarely give feedback on designs during the design process. We are working on many website projects and do not have the time to provide feedback. We usually respond if your request is well thought out and asks specific questions, but a note asking “feedback, please” usually goes unanswered

```html
<!DOCTYPE html>
<html lang="en">
<head>
<meta charset="utf-8">
<title>Fennick Electric</title>
<link href="https://fonts.googleapis.com/css2?family=Lato:wght@400;700;900&display=swap" rel="stylesheet">
<style>
:root{
  --navy:#0b3c8c;
  --navy-deep:#082e6e;
  --yellow:#f5b400;
  --ink:#3a3a3a;
  --muted:#555;
  --dark:#2a2a2a;
  --white:#fff;
  --field:#eef0f4;
}
*{box-sizing:border-box;margin:0;padding:0}
html,body{width:1200px;height:3933px;overflow:hidden}
body{position:relative;background:#fff;font-family:'Lato',sans-serif;color:var(--ink)}
.abs{position:absolute}
.topline{left:0;top:0;width:1200px;height:6px;background:var(--navy)}
.brand{left:111px;top:24px;width:290px;color:var(--navy);font-weight:700;font-size:36px;line-height:42px;letter-spacing:4px;white-space:nowrap}
.brand-dot{display:inline-block;width:14px;height:14px;border-radius:50%;background:var(--yellow);margin-left:6px;vertical-align:middle}
.contact-chip{top:29px;display:flex;align-items:center;gap:22px}
.chip-icon{width:68px;height:68px;border-radius:50%;background:var(--yellow);display:flex;align-items:center;justify-content:center;flex:none}
.chip-label{color:var(--yellow);font-size:15px}
.chip-value{color:#222;font-size:21px;margin-top:6px;white-space:nowrap}
.hero{left:0;top:130px;width:1200px;height:598px;background:linear-gradient(120deg,#8e969e 0%,#5f6870 40%,#7b8288 60%,#a3a89f 85%,#9aa14a 100%)}
.hero-shade{left:0;top:130px;width:1200px;height:598px;background:rgba(20,25,35,.25)}
.nav{left:111px;top:130px;width:755px;height:84px;background:var(--navy);display:flex;align-items:center}
.nav a{position:absolute;color:#fff;font-size:16px;text-decoration:none;transform:translateX(-50%);top:32px;white-space:nowrap}
.nav .active-bar{position:absolute;left:27px;top:78px;width:78px;height:6px;background:var(--yellow)}
.nav-cta{left:866px;top:130px;width:223px;height:84px;background:var(--yellow);color:#fff;font-size:18px;font-weight:700;display:flex;align-items:center;justify-content:center}
.hero-text{left:150px;top:294px;width:900px;text-align:center;color:#fff}
.hero-text .kicker{font-size:30px;line-height:36px}
.hero-text h1{font-size:86px;font-weight:700;line-height:100px;margin-top:2px;white-space:nowrap}
.hero-text p{font-size:21px;line-height:26px;margin-top:18px}
.btn{background:var(--yellow);color:#fff;font-weight:700;display:flex;align-items:center;justify-content:center;border-radius:2px}
.hero-btn{left:524px;top:563px;width:152px;height:40px;font-size:17px}
.round-arrow{width:38px;height:38px;border-radius:50%;display:flex;align-items:center;justify-content:center}
.photo{border-radius:4px}
.section-title{left:0;width:1200px;text-align:center;font-size:42px;font-weight:900;color:var(--navy)}
.section-title span,.about-title span,.contact-title span{color:var(--yellow)}
.about-title{left:657px;top:822px;font-size:42px;font-weight:900;color:var(--navy)}
.about-copy{left:657px;width:432px;font-size:15px;line-height:25.6px;color:var(--muted)}
.about-btn{left:657px;top:1324px;width:154px;height:38px;font-size:17px}
.service{top:1548px;width:313px;height:385px;background:#fff;box-shadow:0 4px 14px rgba(0,0,0,.16);border-radius:3px;text-align:center}
.service .thumb{height:205px;border-radius:3px 3px 0 0}
.service h3{font-size:22px;line-height:26px;color:var(--navy);font-weight:700;margin-top:22px;padding:0 20px}
.service p{font-size:15px;line-height:21.5px;color:var(--muted);margin-top:14px;padding:0 30px}
.service.featured{background:var(--navy)}
.service.featured h3,.service.featured p{color:#fff}
.service .go{position:absolute;left:50%;bottom:-20px;transform:translateX(-50%);width:40px;height:40px;border-radius:50%;background:var(--yellow);display:flex;align-items:center;justify-content:center}
.gal{width:234px;height:307px}
.gal.faded{opacity:.35}
.post{top:2633px;width:313px;height:452px;background:#fff;box-shadow:0 3px 12px rgba(0,0,0,.12);border-radius:3px}
.post .thumb{position:absolute;left:12px;top:13px;width:290px;height:217px;border-radius:6px}
.post .date{position:absolute;left:25px;top:264px;font-size:12px;color:var(--yellow)}
.post h3{position:absolute;left:25px;top:286px;font-size:20px;color:var(--navy);font-weight:700}
.post p{position:absolute;left:25px;top:322px;width:270px;font-size:15px;line-height:22.5px;color:var(--muted)}
.post .more{position:absolute;left:25px;top:400px;font-size:17px;color:var(--yellow)}
.dots{left:575px;top:3106px;display:flex;gap:5px;align-items:center}
.dots i{display:block;width:8px;height:8px;border-radius:50%;background:var(--navy)}
.dots i.on{width:22px;border-radius:4px}
.darkband{left:0;top:3333px;width:1200px;height:546px;background:var(--dark)}
.contact-box{left:111px;top:3202px;width:978px;height:316px;background:linear-gradient(135deg,#1d4f9c,#0b3c8c 60%,#0a3580);border-radius:4px}
.contact-title{left:194px;top:3262px;font-size:42px;font-weight:900;color:#fff}
.contact-info{left:200px;color:#fff;font-size:14px;line-height:22px}
.field{background:var(--field);border-radius:2px;height:40px;font-size:12px;color:#555;padding-left:24px;display:flex;align-items:center}
.submit{left:524px;top:3429px;width:152px;height:39px;font-size:17px}
.foot-h{top:3586px;color:#fff;font-size:20px;font-weight:700}
.foot-rule{top:3621px;width:90px;height:2px;background:var(--yellow)}
.foot-rule::after{content:"";position:absolute;right:-4px;top:-3px;width:8px;height:8px;border-radius:50%;background:var(--yellow)}
.foot-text{color:#fff;font-size:15px;line-height:22.5px}
.foot-links{list-style:none;color:#fff;font-size:15px}
.foot-links li{height:36px;display:flex;align-items:center;gap:16px}
.foot-links li::before{content:"›";font-size:18px}
.subscribe-input{left:847px;top:3706px;width:240px;height:44px;border:1px solid #fff;border-radius:4px;color:#fff;font-size:12px;display:flex;align-items:center;justify-content:space-between;padding:0 18px}
.subscribe-btn{left:847px;top:3764px;width:124px;height:41px;font-size:17px}
.bottombar{left:0;top:3879px;width:1200px;height:54px;background:var(--navy);color:#fff;font-size:13px;display:flex;align-items:center;justify-content:center}
</style>
</head>
<body>
<div class="abs topline"></div>

<div class="abs brand">FENNICK<span class="brand-dot"></span><br>ELECTRIC</div>

<div class="abs contact-chip" style="left:470px">
  <div class="chip-icon"><svg width="30" height="30" viewBox="0 0 24 24"><path fill="#fff" d="M6.6 10.8a15 15 0 0 0 6.6 6.6l2.2-2.2c.3-.3.7-.4 1-.2 1.1.4 2.3.6 3.6.6.6 0 1 .4 1 1V20c0 .6-.4 1-1 1A17 17 0 0 1 3 4c0-.6.4-1 1-1h3.5c.6 0 1 .4 1 1 0 1.3.2 2.5.6 3.6.1.3 0 .7-.2 1z"/></svg></div>
  <div><div class="chip-label">Call us</div><div class="chip-value">+ 1 888 888 8888</div></div>
</div>
<div class="abs contact-chip" style="left:745px">
  <div class="chip-icon"><svg width="30" height="30" viewBox="0 0 24 24"><path fill="#fff" d="M3 6h18v12H3z"/><path fill="none" stroke="#f5b400" stroke-width="2" d="M3 6l9 7 9-7"/></svg></div>
  <div><div class="chip-label">Email</div><div class="chip-value" style="font-size:19px">Info@ Fennick Electric.com</div></div>
</div>

<div class="abs hero" role="img" aria-label="Electrician in a hi-vis vest working on an open switchboard panel"></div>
<div class="abs hero-shade"></div>

<nav class="abs nav">
  <a style="left:66px">Home</a>
  <a style="left:176px">About Us</a>
  <a style="left:297px">Services</a>
  <a style="left:408px">Gallery</a>
  <a style="left:507px">Blog</a>
  <a style="left:619px">Contact Us</a>
  <span class="active-bar"></span>
</nav>
<div class="abs nav-cta">Get Started</div>

<div class="abs round-arrow" style="left:70px;top:410px;background:rgba(255,255,255,.45)"><svg width="18" height="18" viewBox="0 0 24 24"><path fill="none" stroke="#777" stroke-width="3" d="M20 12H5M11 5l-7 7 7 7"/></svg></div>
<div class="abs round-arrow" style="left:1090px;top:410px;background:#fff"><svg width="18" height="18" viewBox="0 0 24 24"><path fill="none" stroke="#555" stroke-width="3" d="M4 12h15M13 5l7 7-7 7"/></svg></div>

<div class="abs hero-text">
  <div class="kicker">Welcome to</div>
  <h1>Fennick Electric</h1>
  <p>Lorem ipsum dolor sit amet, consectetur adipiscing elit,<br>sed do eiusmod tempor incididunt ut labore et dolore<br>magna aliqua.</p>
</div>
<div class="abs btn hero-btn">Get Started</div>

<div class="abs photo" style="left:111px;top:815px;width:462px;height:565px;background:linear-gradient(160deg,#9aa3ab,#6d7780 55%,#c9743a 80%,#4b5560)" role="img" aria-label="Two engineers in hard hats and orange vests inspecting cabling"></div>
<h2 class="abs about-title">About <span>Us</span></h2>
<p class="abs about-copy" style="top:914px">Lorem ipsum dolor sit amet, consectetur adipiscing elit, sed do eiusmod tempor incididunt ut labore et dolore magna aliqua. Ut enim ad minim veniam, quis nostrud exercitation ullamco laboris nisi ut aliquip ex ea commodo consequat. Duis aute irure dolor in reprehenderit in voluptate velit esse cillum dolore eu fugiat nulla pariatur.</p>
<p class="abs about-copy" style="top:1102px">Sed ut perspiciatis unde omnis iste natus error sit voluptatem accusantium doloremque laudantium, totam rem aperiam, eaque ipsa quae ab illo inventore veritatis et quasi architecto beatae vitae dicta sunt explicabo. Nemo enim ipsam voluptatem quia voluptas sit aspernatur aut odit aut fugit, sed quia consequuntur magni dolores eos qui ratione voluptatem sequi nesciunt.</p>
<div class="abs btn about-btn">Read More</div>

<h2 class="abs section-title" style="top:1462px">Our <span>Services</span></h2>
<div class="abs round-arrow" style="left:45px;top:1659px;background:#8ea2c2"><svg width="18" height="18" viewBox="0 0 24 24"><path fill="none" stroke="#fff" stroke-width="3" d="M20 12H5M11 5l-7 7 7 7"/></svg></div>
<div class="abs round-arrow" style="left:1116px;top:1659px;background:var(--navy)"><svg width="18" height="18" viewBox="0 0 24 24"><path fill="none" stroke="#fff" stroke-width="3" d="M4 12h15M13 5l7 7-7 7"/></svg></div>

<div class="abs service" style="left:111px">
  <div class="thumb" style="background:linear-gradient(180deg,#4f7fc4,#8aa9cf 60%,#6b6a55)" role="img" aria-label="Lineman in a bucket lift working on a street light"></div>
  <h3>Government &amp; Public Works</h3>
  <p>Excepteur sint occaecat cupidatat proident, sunt in culpa qui officia deserunt mollit anim id est laborum.</p>
  <div class="go"><svg width="16" height="16" viewBox="0 0 24 24"><path fill="none" stroke="#fff" stroke-width="3.5" d="M4 12h15M13 5l7 7-7 7"/></svg></div>
</div>
<div class="abs service featured" style="left:441px">
  <div class="thumb" style="background:linear-gradient(170deg,#c8ccd2,#9aa4ad 55%,#7e8a5e)" role="img" aria-label="Technician inspecting solar panels in a field"></div>
  <h3>Industrial<br>&amp; Agriculture</h3>
  <p>Excepteur sint occaecat cupidatat proident, sunt in culpa qui officia deserunt mollit anim id est laborum.</p>
  <div class="go"><svg width="16" height="16" viewBox="0 0 24 24"><path fill="none" stroke="#fff" stroke-width="3.5" d="M4 12h15M13 5l7 7-7 7"/></svg></div>
</div>
<div class="abs service" style="left:771px">
  <div class="thumb" style="background:linear-gradient(170deg,#4c5058,#8a8d92 50%,#c45a2a 80%,#5a5e66)" role="img" aria-label="Engineer checking heavy machinery underground"></div>
  <h3>Underground and Civil work</h3>
  <p>Excepteur sint occaecat cupidatat proident, sunt in culpa qui officia deserunt mollit anim id est laborum.</p>
  <div class="go"><svg width="16" height="16" viewBox="0 0 24 24"><path fill="none" stroke="#fff" stroke-width="3.5" d="M4 12h15M13 5l7 7-7 7"/></svg></div>
</div>

<h2 class="abs section-title" style="top:2033px">Our <span>Gallery</span></h2>
<div class="abs gal faded" style="left:-148px;top:2127px;background:linear-gradient(180deg,#6f8fbf,#9fb4d4)" role="img" aria-label="Power transmission tower"></div>
<div class="abs gal" style="left:102px;top:2162px;background:linear-gradient(170deg,#8fb0d8,#3a5a9a 55%,#6a6e58)" role="img" aria-label="Engineer with a laptop at an electrical cabinet"></div>
<div class="abs gal" style="left:351px;top:2127px;background:linear-gradient(170deg,#c9cfd6,#8f9aa6 50%,#2c5aa8)" role="img" aria-label="Electrician in a hard hat testing a panel"></div>
<div class="abs gal" style="left:600px;top:2162px;background:linear-gradient(180deg,#d9dde2,#a9b0b8 60%,#c9743a 80%,#8a8f95)" role="img" aria-label="Two workers in orange vests beside tall server racks"></div>
<div class="abs gal" style="left:849px;top:2127px;background:linear-gradient(170deg,#b7bcc1,#6d747b 45%,#3f5f9a 70%,#c23a2a)" role="img" aria-label="Gloved hands wiring a switchgear unit"></div>
<div class="abs gal faded" style="left:1099px;top:2162px;background:linear-gradient(180deg,#a8bad6,#c8d4e6)" role="img" aria-label="Overhead power lines"></div>

<h2 class="abs section-title" style="top:2548px">Our <span>Blog</span></h2>
<div class="abs post" style="left:111px">
  <div class="thumb" style="background:linear-gradient(170deg,#c7ccd1,#8e979f 50%,#c9c23a)" role="img" aria-label="Two electricians in hard hats shaking hands on site"></div>
  <div class="date">Sep 10 , 2024</div><h3>Lorem Ipsum</h3>
  <p>Excepteur sint occaecat cupidatat non quis nostrud exercitation ullamco deserunt mollit anim id est laborum.</p>
  <div class="more">Read More...</div>
</div>
<div class="abs post" style="left:441px">
  <div class="thumb" style="background:linear-gradient(170deg,#5d646c,#a4aab0 50%,#c7c43a 70%,#2a2d33)" role="img" aria-label="Workers in hi-vis vests at a control panel wall"></div>
  <div class="date">Sep 10 , 2024</div><h3>Lorem Ipsum</h3>
  <p>Excepteur sint occaecat cupidatat non quis nostrud exercitation ullamco deserunt mollit anim id est laborum.</p>
  <div class="more">Read More...</div>
</div>
<div class="abs post" style="left:771px">
  <div class="thumb" style="background:linear-gradient(170deg,#a0523a,#7a4a3a 45%,#d8c9b6 65%,#b03a2a)" role="img" aria-label="Electrician's hands with tools and cables on a workbench"></div>
  <div class="date">Sep 10 , 2024</div><h3>Lorem Ipsum</h3>
  <p>Excepteur sint occaecat cupidatat non quis nostrud exercitation ullamco deserunt mollit anim id est laborum.</p>
  <div class="more">Read More...</div>
</div>
<div class="abs dots"><i class="on"></i><i></i><i></i></div>

<div class="abs darkband"></div>
<div class="abs contact-box"></div>
<h2 class="abs contact-title">Contact <span>Us</span></h2>
<div class="abs contact-info" style="top:3335px">123,electrical contractor in California<br>Company Na 123456.</div>
<div class="abs contact-info" style="top:3397px">+ 1 888 888 8888</div>
<div class="abs contact-info" style="top:3434px">Info Fennick Electric.com</div>
<div class="abs field" style="left:521px;top:3260px;width:525px">Full Name</div>
<div class="abs field" style="left:521px;top:3315px;width:256px">Email</div>
<div class="abs field" style="left:788px;top:3315px;width:258px">Phone</div>
<div class="abs field" style="left:521px;top:3370px;width:525px">Message</div>
<div class="abs btn submit">Submit</div>

<div class="abs foot-h" style="left:116px">About Company</div>
<div class="abs foot-rule" style="left:116px;width:90px"></div>
<p class="abs foot-text" style="left:116px;top:3648px;width:235px">Lorem ipsum dolor sit amet, consectetur adipiscing elit, sed do eiusmod tempor incididunt ut labore et dolore magna aliqua. Quis ipsum suspendisse ultrices gravida.</p>

<div class="abs foot-h" style="left:386px">Quick Links</div>
<div class="abs foot-rule" style="left:386px;width:85px"></div>
<ul class="abs foot-links" style="left:386px;top:3640px"><li>Home</li><li>About Us</li><li>Services</li><li>Gallery</li><li>Blog</li></ul>

<div class="abs foot-h" style="left:577px">Other Links</div>
<div class="abs foot-rule" style="left:577px;width:85px"></div>
<ul class="abs foot-links" style="left:577px;top:3640px"><li>Contact Us</li><li>Terms &amp; Conditions</li><li>Privacy Policy</li><li>Cookies Policy</li><li>Copyrights Notification</li></ul>

<div class="abs foot-h" style="left:847px">News Subscription</div>
<div class="abs foot-rule" style="left:847px;width:85px"></div>
<p class="abs foot-text" style="left:847px;top:3648px;width:240px;font-size:14px;line-height:20px">Lorem ipsum dolor sit amet, consectetur incididunt ut aliqua.</p>
<div class="abs subscribe-input">Email Address<svg width="14" height="14" viewBox="0 0 24 24"><path fill="none" stroke="#f5b400" stroke-width="2.5" d="M3 6h18v12H3zM3 6l9 7 9-7"/></svg></div>
<div class="abs btn subscribe-btn">Subscribe</div>

<div class="abs bottombar">Copyright © 2024 &nbsp;Fennick Electric. All rights reserved.</div>
</body>
</html>
```